Insurance Agency website design for Brellow Cover Insurance, LP

Build a website for Brellow Cover Insurance, LP which sells Homeowners, Auto, Renters, Condo, Flood, Disability, Life, Umbrella, and health insurance. We need the coolest insurance agency website out there to get quotes, contact us, or get additional information. Please list the following insurance companies we work with: Varnix, Ostle, Meridale Mutual, Quillor, Dunmarrow, KGZ, and Pellwick.

Make a design similar to https://www.fernagentry.com/

Selling personal insurance policies

```html
<!DOCTYPE html>
<html lang="en">
<head>
<meta charset="utf-8">
<title>Brellow Cover Insurance, LP</title>
<link href="https://fonts.googleapis.com/css2?family=Open+Sans:wght@400;600;700;800&display=swap" rel="stylesheet">
<style>
:root{
  --blue:#1f70b4;
  --blue-dark:#15578e;
  --green:#25a12a;
  --ink:#1d1d1d;
  --muted:#555;
  --line:#e3e3e3;
  --footer:#1c1c1c;
  --white:#fff;
}
*{box-sizing:border-box;margin:0;padding:0}
html,body{width:1200px;height:3432px;overflow:hidden}
body{font-family:"Open Sans",Arial,sans-serif;color:var(--ink);background:var(--white);position:relative}
.abs{position:absolute}
.btn{display:inline-block;background:var(--green);color:var(--white);font-weight:700;border-radius:4px;text-decoration:none}

/* header */
.site-header{left:0;top:0;width:1200px;height:70px;background:var(--white);z-index:2;box-shadow:0 2px 6px rgba(0,0,0,.08)}
.brand{left:120px;top:14px;display:flex;align-items:center;gap:12px}
.brand-dot{width:40px;height:40px;border-radius:50%;background:var(--blue)}
.brand-name{font-size:22px;font-weight:800;color:var(--blue)}
.nav{right:120px;top:16px;display:flex;align-items:center;gap:26px;font-size:15px}
.nav a{color:var(--ink);text-decoration:none}
.nav a.active{color:var(--blue);border-bottom:2px solid var(--blue);padding-bottom:3px}
.nav .btn{padding:9px 16px;font-size:14px}

/* hero */
.hero{left:0;top:70px;width:1200px;height:590px;background:linear-gradient(90deg,#1e2a36 0%,#3c4a57 45%,#8a94a0 100%)}
.hero h1{left:115px;top:130px;width:520px;color:var(--white);font-size:62px;line-height:1.12;font-weight:800}
.hero .btn{left:115px;top:450px;padding:12px 20px;font-size:15px}

/* partners */
.section-title{width:1200px;text-align:center;font-size:40px;font-weight:600}
.section-title span{color:var(--blue)}
.partners{left:0;top:705px}
.partner-row{left:30px;top:808px;width:1140px;display:flex;justify-content:space-between;align-items:center;font-weight:700;font-size:22px}
.partner-row span:nth-child(odd){color:#333}
.partner-row span:nth-child(even){color:var(--blue)}

/* about */
.about-img{left:112px;top:940px;width:340px;height:310px;border-radius:6px;background:linear-gradient(160deg,#dbe6ee,#a9c4d8 55%,#5d8db8)}
.about-text{left:640px;top:925px;width:450px}
.about-text h2{font-size:44px;font-weight:600;margin-bottom:20px}
.about-text h2 span{color:var(--blue)}
.about-text p{font-size:15px;line-height:1.75;color:var(--muted);margin-bottom:12px}
.about-text b{color:var(--blue)}

/* quote band */
.quote-left{left:0;top:1400px;width:360px;height:380px;background:linear-gradient(135deg,#e9ecef,#b8c2cb)}
.quote-panel{left:350px;top:1400px;width:500px;height:380px;background:var(--blue);color:var(--white);text-align:center;padding:34px 50px}
.quote-panel h2{font-size:42px;font-weight:700;margin-bottom:20px}
.quote-panel p{font-size:13px;line-height:1.7;margin-bottom:12px;opacity:.95}
.quote-right{left:850px;top:1400px;width:350px;height:380px;background:linear-gradient(135deg,#9aa7b2,#5d6b77)}

/* offers */
.offers{left:0;top:1860px}
.offer-card{top:1950px;width:268px;height:270px;border:1px solid var(--line);background:var(--white);box-shadow:0 3px 10px rgba(0,0,0,.08)}
.offer-card .photo{width:100%;height:210px}
.offer-card .label{height:58px;display:flex;align-items:center;justify-content:center;font-size:17px}
.offer-card.featured{border-top:4px solid var(--green)}
.offer-card.featured .photo{background:linear-gradient(180deg,#4fb34a,#2f8f35)}
.offer-card.featured .label{align-items:flex-end;padding-bottom:8px}
.home-badge{left:106px;top:150px;width:54px;height:54px;border-radius:50%;background:var(--white);border:2px solid var(--green);display:flex;align-items:center;justify-content:center}
.view-all{left:556px;top:2250px;padding:9px 16px;font-size:14px}

/* connect */
.connect{left:112px;top:2360px;width:976px;height:345px;background:var(--blue);border-radius:10px}
.connect-inner{left:50px;top:30px;width:500px;color:var(--white)}
.connect-inner h2{font-size:38px;font-weight:700;margin-bottom:8px}
.connect-inner p{font-size:13px;line-height:1.6;margin-bottom:18px}
.connect-inner label{display:block;font-size:13px;font-weight:600;margin-bottom:6px}
.field{width:440px;height:40px;background:var(--white);border-radius:4px;color:#999;font-size:13px;padding:11px 14px;margin-bottom:16px}
.field.short{width:300px}
.connect-inner .btn{padding:9px 16px;font-size:13px}
.connect-photo{left:600px;top:-20px;width:400px;height:385px;border-radius:120px 20px 20px 150px;background:linear-gradient(135deg,#d9d4cc,#8f8679);border:6px solid var(--white)}

/* footer */
.site-footer{left:0;top:2790px;width:1200px;height:642px;background:var(--footer);color:var(--white)}
.footer-brand{left:125px;top:120px;text-align:center}
.footer-brand .brand-dot{margin:0 auto 14px;width:70px;height:70px}
.footer-brand .name{font-size:22px;font-weight:700}
.socials{display:flex;gap:10px;justify-content:center;margin-top:16px}
.socials i{width:26px;height:26px;border-radius:50%;background:var(--blue)}
.footer-col{top:200px}
.footer-col h3{font-size:18px;font-weight:700;margin-bottom:14px}
.footer-col li{list-style:none;font-size:14px;margin-bottom:10px;color:#ddd}
.contact li{display:flex;align-items:center;gap:10px}
.copyright{left:0;top:3395px;width:1200px;text-align:center;font-size:12px;color:#bbb}
.footer-rule{left:0;top:3375px;width:1200px;height:1px;background:#333}
</style>
</head>
<body>

<header class="site-header abs">
  <div class="brand abs"><div class="brand-dot"></div><div class="brand-name">Brellow Cover Insurance, LP</div></div>
  <nav class="nav abs"><a class="active" href="#">Home</a><a href="#">About</a><a class="btn" href="#">Get a Quote</a></nav>
</header>

<section class="hero abs" role="img" aria-label="Agent consulting with a couple at a table in a bright modern office">
  <h1 class="abs">Insurance that protects your property and your life</h1>
  <a class="btn abs" href="#">Start Coverage Now</a>
</section>

<h2 class="section-title partners abs">Companies We <span>Work With</span></h2>
<div class="partner-row abs">
  <span>Varnix</span><span>Ostle</span><span>Meridale Mutual</span><span>Quillor</span><span>Dunmarrow</span><span>KGZ</span><span>Pellwick</span>
</div>

<div class="about-img abs" role="img" aria-label="Blue umbrella sheltering a small model house"></div>
<div class="about-text abs">
  <h2>About <span>Us</span></h2>
  <p><b>Brellow Cover Insurance</b> is a full-service, independent insurance agency with over three decades of experience in delivering comprehensive insurance solutions to individuals.</p>
  <p>We proudly offer a diverse portfolio of products from more than 20 of the most reputable and financially secure companies in the industry. Our dedicated team of over 10 skilled professionals is committed to customizing these products and services to meet the unique needs of each client.</p>
  <p>At Brellow Cover Insurance, our experts are focused on addressing the individual needs of our clients, ensuring exceptional service and support at every step.</p>
</div>

<div class="quote-left abs" role="img" aria-label="Agent handing a model house and keys to a client"></div>
<div class="quote-panel abs">
  <h2>Get a Quote</h2>
  <p>We believe that securing your home is one of the most important decisions you can make. Choosing a comprehensive insurance plan is essential to understanding your coverage options and ensuring that your property is adequately protected against unforeseen events.</p>
  <p>Our team of experienced professionals is here to guide you through the process, helping you find the right policy that meets your specific needs and budget. Don't leave your home's safety to chance - get a quote today and take the first step towards peace of mind.</p>
</div>
<div class="quote-right abs" role="img" aria-label="Agent shaking hands with a couple across a desk"></div>

<h2 class="section-title offers abs">What <span>We Offer</span></h2>
<div class="offer-card abs" style="left:195px">
  <div class="photo" role="img" aria-label="Smiling man with crossed arms" style="background:linear-gradient(180deg,#f1f1f1,#cfd8e2)"></div>
  <div class="label">Auto</div>
</div>
<div class="offer-card featured abs" style="left:466px">
  <div class="photo" role="img" aria-label="Smiling woman on a green background"></div>
  <div class="home-badge abs"><svg width="26" height="26" viewBox="0 0 24 24"><path d="M3 11 12 3l9 8v10h-6v-6H9v6H3z" fill="#25a12a"/></svg></div>
  <div class="label">Home</div>
</div>
<div class="offer-card abs" style="left:737px">
  <div class="photo" role="img" aria-label="Man in a plaid shirt with crossed arms" style="background:linear-gradient(180deg,#f1f1f1,#d4dde5)"></div>
  <div class="label">Rv/Motorhome</div>
</div>
<a class="btn view-all abs" href="#">View All</a>

<section class="connect abs">
  <div class="connect-inner abs">
    <h2>Let's Connect With Us</h2>
    <p>The address of your personal property will help in finding the right local agent for you.</p>
    <label>Enter the address of your insurable property</label>
    <div class="field">Start typing your street address</div>
    <label>Zip code (required)</label>
    <div class="field short">ZIP code</div>
    <a class="btn" href="#">Submit</a>
  </div>
  <div class="connect-photo abs" role="img" aria-label="Team meeting around a laptop in an office"></div>
</section>

<footer class="site-footer abs">
  <div class="footer-brand abs">
    <div class="brand-dot"></div>
    <div class="name">Brellow Cover Insurance, LP</div>
    <div class="socials"><i></i><i></i><i></i><i></i></div>
  </div>
  <div class="footer-col abs" style="left:510px"><h3>Quick Links</h3><ul><li>Home</li><li>About</li><li>Get a Quote</li></ul></div>
  <div class="footer-col abs" style="left:665px"><h3>Other Links</h3><ul><li>Privacy Policy</li><li>Terms &amp; Conditions</li><li>Disclaimer</li></ul></div>
  <div class="footer-col contact abs" style="left:860px"><h3>Contact Info</h3><ul>
    <li><svg width="16" height="16" viewBox="0 0 24 24"><path d="M12 2a7 7 0 0 0-7 7c0 5 7 13 7 13s7-8 7-13a7 7 0 0 0-7-7zm0 9.5A2.5 2.5 0 1 1 12 6.5a2.5 2.5 0 0 1 0 5z" fill="#fff"/></svg>12 Alder Row, USA - 40791</li>
    <li><svg width="16" height="16" viewBox="0 0 24 24"><path d="M6.6 10.8a15 15 0 0 0 6.6 6.6l2.2-2.2c.3-.3.7-.4 1-.2 1.1.4 2.3.6 3.6.6.6 0 1 .4 1 1V20c0 .6-.4 1-1 1A17 17 0 0 1 3 4c0-.6.4-1 1-1h3.5c.6 0 1 .4 1 1 0 1.3.2 2.5.6 3.6.1.3 0 .7-.2 1z" fill="#fff"/></svg>+1 555 010 0142</li>
    <li><svg width="16" height="16" viewBox="0 0 24 24"><path d="M3 5h18v14H3zm2 2v.5l7 4.5 7-4.5V7z" fill="#fff"/></svg>info@brellowcover.com</li>
  </ul></div>
</footer>
<div class="footer-rule abs"></div>
<div class="copyright abs">Copyright © 2024 Brellow Cover Insurance, LP. All rights reserved.</div>

</body>
</html>
```